Redesign Website - Current one too plain

The description is in the uploaded file. Please let me know if you need any more information. I'd prefer it if someone could implement the design to a WordPress site but the best design will win, regardless.
I would like the forms to look nice as well
UPDATE:
I don't think we can use the images that I provided, I think they make the site look a bit 'cheap' and I really don't know how to replace them. One thought I have had is to make the "Simple, Unique, Effective" a second feature on the right side of the page with the search on the left
Target Market(s)
Small companies, private sellers of cars and people who rent their caravan/holiday home out
Industry/Entity Type
Advertising
Number of Pages Required
3 page
Colors
Designer to choose colors to be used in the design.
Look and feel
Each slider illustrates characteristics of the customer's brand and the style your logo design should communicate.

```html
<!DOCTYPE html>
<html lang="en">
<head>
<meta charset="utf-8">
<title>Marko – Advertise with a code</title>
<link rel="stylesheet" href="https://fonts.googleapis.com/css2?family=Lato:wght@400;700;900&family=Poppins:wght@500&family=Roboto:wght@400;500&display=swap">
<style>
:root{
  --ink:#222222;
  --panel:#242424;
  --lime:#e2ff00;
  --sky:#00c6f5;
  --mist:#f3f3f3;
  --soft:#e4e4e4;
  --grey:#6f6f6f;
  --white:#ffffff;
}
*{margin:0;padding:0;box-sizing:border-box}
html,body{width:1200px;height:2666px;overflow:hidden;background:var(--white)}
body{position:relative;font-family:"Lato",sans-serif;color:var(--ink)}
.abs{position:absolute}

/* header */
.brand{position:absolute;display:flex;align-items:center;gap:14px;font-weight:900;letter-spacing:9px}
.brand-dot{width:28px;height:28px;border-radius:50%}
.site-header .brand{left:111px;top:32px;font-size:44px;color:var(--ink)}
.site-header .brand-dot{background:var(--ink)}
.main-nav{position:absolute;top:40px;left:0;width:1200px;font-size:18px}
.main-nav a{position:absolute;transform:translateX(-50%);color:var(--ink);text-decoration:none;white-space:nowrap}

/* hero */
.hero-rim{left:70px;top:100px;width:1060px;height:600px;background:var(--lime);border-radius:96px;transform:rotate(1.2deg)}
.hero{left:78px;top:111px;width:1045px;height:582px;background:var(--panel);border-radius:92px;overflow:hidden}
.hero-glow{left:560px;top:80px;width:420px;height:480px;border-radius:50%;background:radial-gradient(circle,#3a3a3a 0%,rgba(36,36,36,0) 70%)}
.code-picker{left:195px;top:232px;width:200px;text-align:center}
.code-value{font-size:140px;line-height:1;color:var(--lime);font-weight:400;letter-spacing:4px}
.chev{position:absolute;width:18px;height:12px}
.chip{position:absolute;top:446px;height:38px;border-radius:19px;background:var(--white);font-weight:700;font-size:15px;display:flex;align-items:center;justify-content:center;color:var(--ink)}
.search-bar{left:138px;top:511px;width:324px;height:45px;border-radius:23px;background:var(--lime);display:flex;align-items:center;justify-content:space-between;padding:0 16px 0 24px;font-weight:700;font-size:16px}
.vehicle{position:absolute;border-radius:14px}

/* about */
.about-mark{left:145px;top:771px;width:401px;height:461px}
.about-title{left:604px;top:764px;font-size:35px;font-weight:900}
.about-copy{left:604px;top:812px;width:485px;font-size:15px;line-height:29px;text-align:justify}
.about-copy p+p{margin-top:29px}
.btn-read{left:604px;top:1151px;width:164px;height:60px;border-radius:30px;background:var(--sky);color:var(--ink);font-size:19px;font-weight:700;display:flex;align-items:center;justify-content:center;box-shadow:0 4px 10px rgba(0,0,0,.15)}

/* features */
.features{left:112px;top:1286px;width:977px;height:438px;background:var(--mist);border-radius:64px}
.feature{position:absolute;top:1347px;width:259px;height:307px;background:var(--panel);border-radius:6px;text-align:center;box-shadow:0 6px 12px rgba(0,0,0,.15)}
.feature::after{content:"";position:absolute;left:20px;right:20px;bottom:-6px;height:6px;background:var(--sky);border-radius:0 0 4px 4px}
.feature-icon{width:126px;height:126px;border-radius:50%;background:var(--lime);margin:30px auto 0;display:flex;align-items:center;justify-content:center}
.feature h3{margin-top:38px;color:var(--lime);font-size:25px;font-weight:400;letter-spacing:.5px}
.feature p{margin:10px auto 0;width:210px;color:#a8a8a8;font-size:14px;line-height:25px}

/* testimonials */
.section-title{left:0;width:1200px;top:1778px;text-align:center;font-size:36px;font-weight:900}
.avatar{position:absolute;border-radius:50%}
.dot{position:absolute;border-radius:50%}
.quote-mark{position:absolute;font-family:"Lato",sans-serif;font-weight:900;font-size:250px;line-height:1;color:var(--soft)}
.client-name{left:0;width:1200px;top:1998px;text-align:center;font-size:21px}
.client-place{left:0;width:1190px;top:2034px;text-align:center;font-family:"Poppins",sans-serif;font-size:12px;color:var(--grey)}
.stars{left:531px;top:2058px;width:130px;height:28px}
.client-quote{left:260px;top:2096px;width:670px;text-align:center;font-size:15px;line-height:26px}

/* footer */
.site-footer{left:0;top:2238px;width:1200px;height:428px;background:var(--panel);color:var(--white)}
.site-footer .brand{left:109px;top:72px;font-size:30px;color:var(--lime);letter-spacing:7px;gap:10px}
.site-footer .brand-dot{background:var(--lime);width:22px;height:22px}
.footer-head{position:absolute;top:70px;font-size:18px;font-weight:700}
.contact-item{position:absolute;left:315px;display:flex;align-items:center;gap:18px;font-size:13px;line-height:19px}
.contact-icon{width:37px;height:37px;border-radius:50%;border:1.5px solid var(--white);display:flex;align-items:center;justify-content:center;flex:none}
.field{position:absolute;background:var(--white);border:1px solid #cfcfcf;font-family:"Roboto",sans-serif;font-size:11px;color:#888;padding:9px 12px}
.btn-submit{position:absolute;left:995px;top:289px;width:94px;height:37px;border-radius:19px;background:var(--sky);color:var(--ink);font-family:"Roboto",sans-serif;font-weight:500;font-size:13px;display:flex;align-items:center;justify-content:center}
.footer-rule{position:absolute;left:112px;top:348px;width:977px;height:1px;background:#bdbdbd}
.copyright{position:absolute;left:0;width:1200px;top:379px;text-align:center;font-size:13px}
</style>
</head>
<body>

<header class="site-header">
  <div class="brand"><span class="brand-dot"></span>MARKO</div>
  <nav class="main-nav">
    <a style="left:618px">Home</a>
    <a style="left:730px">Advertise</a>
    <a style="left:849px">Contact</a>
    <a style="left:963px">Register</a>
    <a style="left:1067px">Login</a>
  </nav>
</header>

<div class="hero-rim abs"></div>
<section class="hero abs">
  <div class="hero-glow abs"></div>
  <div class="vehicle" role="img" aria-label="Static caravan with yellow code plate" style="left:605px;top:170px;width:235px;height:130px;background:linear-gradient(180deg,#d9d9d6,#9c9b96)"></div>
  <div class="vehicle" role="img" aria-label="Silver SUV with yellow code plate" style="left:440px;top:298px;width:242px;height:105px;background:linear-gradient(180deg,#b9b9b9,#6a6a6a)"></div>
  <div class="vehicle" role="img" aria-label="Silver commercial van with yellow code plate" style="left:746px;top:292px;width:262px;height:111px;background:linear-gradient(180deg,#c8c8c8,#777)"></div>
</section>

<div class="code-picker abs" style="top:232px">
  <svg class="chev" style="left:57px;top:8px" viewBox="0 0 18 12"><path d="M2 10 9 3l7 7" fill="none" stroke="#fff" stroke-width="2"/></svg>
  <svg class="chev" style="left:153px;top:8px" viewBox="0 0 18 12"><path d="M2 10 9 3l7 7" fill="none" stroke="#fff" stroke-width="2"/></svg>
  <div class="code-value" style="margin-top:28px">A1</div>
  <svg class="chev" style="left:57px;top:180px" viewBox="0 0 18 12"><path d="M2 2l7 7 7-7" fill="none" stroke="#fff" stroke-width="2"/></svg>
  <svg class="chev" style="left:153px;top:180px" viewBox="0 0 18 12"><path d="M2 2l7 7 7-7" fill="none" stroke="#fff" stroke-width="2"/></svg>
</div>

<div class="chip" style="left:139px;width:88px">Car</div>
<div class="chip" style="left:246px;width:88px">Caravan</div>
<div class="chip" style="left:353px;width:88px">Company</div>
<div class="search-bar abs">Search
  <svg width="14" height="14" viewBox="0 0 14 14"><circle cx="6" cy="6" r="4.3" fill="none" stroke="#222" stroke-width="2"/><path d="M9.2 9.2 13 13" stroke="#222" stroke-width="2.2" stroke-linecap="round"/></svg>
</div>

<section>
  <svg class="about-mark abs" viewBox="0 0 401 461" role="img" aria-label="Bold black blob with lime offset">
    <circle cx="216" cy="225" r="180" fill="#e2ff00"/>
    <circle cx="200" cy="235" r="180" fill="#000"/>
  </svg>
  <h2 class="about-title abs">ABOUT MARKO</h2>
  <div class="about-copy abs">
    <p>At vero eos et accusamus et iusto odio dignissimos ducimus qui blanditiis praesentium voluptatum deleniti atque corrupti quos dolores et quas molestias excepturi sint occaecati cupiditate non provident, similique sunt in culpa qui officia deserunt mollitia animi, id est laborum et dolorum fuga.Nam libero tempore, cum soluta nobis est eligendi optio cumque nihil impedit quo minus id quod maxime placeat facere possimus, omnis voluptas assumenda est, omnis dolor repellendus.</p>
    <p>Itaque earum rerum hic tenetur a sapiente delectus, ut aut reiciendis voluptatibus maiores alias consequatur aut perferendis doloribus asperiores repellat.</p>
  </div>
  <div class="btn-read abs">Read More</div>
</section>

<section>
  <div class="features abs"></div>
  <article class="feature" style="left:165px">
    <div class="feature-icon"><svg width="44" height="44" viewBox="0 0 44 44" fill="none" stroke="#222" stroke-width="2"><circle cx="22" cy="22" r="18"/><circle cx="22" cy="22" r="11"/><circle cx="22" cy="22" r="4"/><path d="M22 22 38 6"/></svg></div>
    <h3>SIMPLE</h3><p>Create &nbsp;your advert and display your code</p>
  </article>
  <article class="feature" style="left:475px">
    <div class="feature-icon"><svg width="44" height="44" viewBox="0 0 44 44" fill="none" stroke="#222" stroke-width="2"><circle cx="22" cy="22" r="16"/><path d="M22 13l3 6 6 1-4.5 4 1 6-5.5-3-5.5 3 1-6-4.5-4 6-1z"/></svg></div>
    <h3>UNIQUE</h3><p>Customers find you by an easy-to-remember code</p>
  </article>
  <article class="feature" style="left:786px">
    <div class="feature-icon"><svg width="44" height="44" viewBox="0 0 44 44" fill="none" stroke="#222" stroke-width="2"><path d="M5 38h34M6 30l10-9 7 6 15-16"/><path d="M30 11h8v8"/></svg></div>
    <h3>EFFECTIVE</h3><p>Customers are directed to you and not a list of your competitors</p>
  </article>
</section>

<section>
  <h2 class="section-title abs">TESTIMONIALS</h2>
  <div class="avatar" role="img" aria-label="Portrait of featured client" style="left:526px;top:1843px;width:134px;height:134px;background:linear-gradient(160deg,#f0b98a,#e8a273)"></div>
  <div class="avatar" role="img" aria-label="Portrait of client" style="left:122px;top:1917px;width:66px;height:66px;background:linear-gradient(160deg,#f1c7a8,#c98d6c)"></div>
  <div class="avatar" role="img" aria-label="Portrait of client" style="left:999px;top:1842px;width:46px;height:46px;background:linear-gradient(160deg,#d8c9c0,#7a5a4c)"></div>
  <div class="dot" style="left:366px;top:1954px;width:13px;height:13px;background:#ef1b2d"></div>
  <div class="dot" style="left:881px;top:1917px;width:7px;height:7px;background:#3f82e0"></div>
  <div class="quote-mark" style="left:150px;top:1990px">&ldquo;</div>
  <div class="quote-mark" style="left:940px;top:2092px">&rdquo;</div>
  <div class="client-name abs">Daniel Whitmore</div>
  <div class="client-place abs">United States</div>
  <svg class="stars abs" viewBox="0 0 130 28" fill="#f5b82e">
    <path id="st" d="M13 1l3.6 8 8.4.8-6.4 5.6 2 8.4L13 19.4 5.4 23.8l2-8.4L1 9.8 9.4 9z"/>
    <use href="#st" x="26"/><use href="#st" x="52"/><use href="#st" x="78"/><use href="#st" x="104"/>
  </svg>
  <p class="client-quote abs">Itaque earum rerum hic tenetur a sapiente delectus, ut aut reiciendis voluptatibus maiores alias. Consequatur aut perferendis doloribus asperiores repellat.Et harum quidem rerum f acilis est et expedita distinctio.</p>
</section>

<footer class="site-footer abs">
  <div class="brand"><span class="brand-dot"></span>MARKO</div>
  <h4 class="footer-head" style="left:315px">CONTACT INFORMATION</h4>
  <div class="contact-item" style="top:113px"><span class="contact-icon"><svg width="12" height="16" viewBox="0 0 12 16"><path d="M6 1a5 5 0 0 1 5 5c0 4-5 9-5 9S1 10 1 6a5 5 0 0 1 5-5z" fill="none" stroke="#00c6f5" stroke-width="1.8"/><circle cx="6" cy="6" r="1.8" fill="#00c6f5"/></svg></span>123,Lorem ipsum dolor sit amet,<br>tetur adipiscing elit</div>
  <div class="contact-item" style="top:165px"><span class="contact-icon"><svg width="14" height="14" viewBox="0 0 14 14"><path d="M3 1l3 3-1.5 2a8 8 0 0 0 3.5 3.5L10 8l3 3-2 2C6 13 1 8 1 3z" fill="#00c6f5"/></svg></span>Phone : +1 555 010 0199</div>
  <div class="contact-item" style="top:213px"><span class="contact-icon"><svg width="15" height="11" viewBox="0 0 15 11"><rect width="15" height="11" rx="1.5" fill="#00c6f5"/><path d="M1 1.5l6.5 5 6.5-5" fill="none" stroke="#242424" stroke-width="1.3"/></svg></span>Email : info@marko-ads.com</div>
  <h4 class="footer-head" style="left:596px">GET IN TOUCH:</h4>
  <div class="field" style="left:598px;top:113px;width:240px;height:32px">Name :</div>
  <div class="field" style="left:848px;top:113px;width:241px;height:32px">Phone :</div>
  <div class="field" style="left:598px;top:156px;width:491px;height:32px">Email :</div>
  <div class="field" style="left:598px;top:199px;width:491px;height:71px">Message :</div>
  <div class="btn-submit">SUBMIT</div>
  <div class="footer-rule"></div>
  <p class="copyright">Copyrights © 2023.Marko. All Rights Reserved. &nbsp;| &nbsp;Privacy policy</p>
</footer>

</body>
</html>
```